My business is Property developing Stationary

I want business card and stationery. Please have the formate so I can edit details on card and stationary.

Please see my logo and on the back of the card I want it same red as my logo and I will provide copy that I want on the back of the card.

Also need an email signature

On the business card and email signature add below copy:
Project Management- Acquisitions- Syndicates- Joint Ventures

Target Market(s)

Property investors

Industry/Entity Type

Business

Requirements
Must have
• Reflect my Logo

```html
<!DOCTYPE html>
<html lang="en">
<head>
<meta charset="utf-8">
<title>Verano Property – Business Card</title>
<link rel="stylesheet" href="https://fonts.googleapis.com/css2?family=Mulish:wght@400;600;800&display=swap">
<style>
  :root {
    --brand-red: #d8362b;
    --ink: #1c1c1c;
    --text-grey: #3a3a3a;
    --paper: #f7f7f6;
    --backdrop: #262626;
    --white: #ffffff;
  }
  * { margin: 0; padding: 0; box-sizing: border-box; }
  html, body {
    width: 1200px; height: 1000px; overflow: hidden;
    background: var(--backdrop);
    font-family: "Mulish", Arial, sans-serif;
  }
  .card {
    position: absolute; top: 358px;
    width: 510px; height: 284px; overflow: hidden;
  }
  .card-front { left: 72px; background: var(--paper); }
  .card-back { left: 624px; background: var(--brand-red); }
  .card-graphics { position: absolute; inset: 0; }

  .holder-name {
    position: absolute; left: 21px; top: 50px;
    color: var(--brand-red); font-weight: 800; font-size: 16px; letter-spacing: 0.3px;
  }
  .holder-title {
    position: absolute; left: 21px; top: 71px;
    color: var(--text-grey); font-size: 13px;
  }
  .contact-list {
    position: absolute; left: 21px; top: 110px; list-style: none;
  }
  .contact-list li {
    display: flex; align-items: center; height: 16px;
    font-size: 12.5px; color: var(--text-grey);
  }
  .contact-list svg { width: 11px; height: 11px; margin-right: 10px; flex: none; }
  .address {
    position: absolute; left: 21px; top: 192px;
    font-size: 12.5px; line-height: 15px; color: var(--text-grey);
  }
  .services {
    position: absolute; left: 21px; top: 242px;
    font-size: 11px; color: var(--ink);
  }
  .brand {
    position: absolute; font-weight: 800; letter-spacing: 0.5px; white-space: nowrap;
  }
  .card-front .brand { right: 46px; top: 54px; font-size: 28px; color: var(--brand-red); }
  .card-back .brand { right: 48px; top: 62px; font-size: 34px; color: var(--white); }
  .back-web {
    position: absolute; right: 48px; top: 233px;
    font-size: 12.5px; color: var(--white);
  }
</style>
</head>
<body>

<section class="card card-front" aria-label="Business card front">
  <svg class="card-graphics" viewBox="0 0 510 284" aria-hidden="true">
    <polygon points="0,270 373,270 359,284 0,284" fill="var(--brand-red)"/>
    <polygon points="510,157 510,197 423,284 383,284" fill="var(--ink)"/>
    <polygon points="510,230 510,284 456,284" fill="var(--brand-red)"/>
  </svg>

  <div class="holder-name">LUCAS FERREIRA</div>
  <div class="holder-title">Managing Director</div>

  <ul class="contact-list">
    <li>
      <svg viewBox="0 0 11 11"><rect width="11" height="11" rx="2" fill="var(--brand-red)"/><rect x="3.5" y="2" width="4" height="7" rx="0.8" fill="none" stroke="#fff" stroke-width="1"/></svg>
      +61 (0) 400 555 018
    </li>
    <li>
      <svg viewBox="0 0 11 11"><rect width="11" height="11" rx="2" fill="var(--brand-red)"/><path d="M3 2.5 L4.5 2.5 L5 4 L4.2 4.8 Q5 6.2 6.2 6.8 L7 6 L8.5 6.5 L8.5 8 Q5 8.5 2.5 4 Z" fill="#fff"/></svg>
      +61 (0) 400 555 019
    </li>
    <li>
      <svg viewBox="0 0 11 11"><rect width="11" height="11" rx="2" fill="var(--brand-red)"/><rect x="2" y="3" width="7" height="5" fill="none" stroke="#fff" stroke-width="1"/><path d="M2 3 L5.5 6 L9 3" fill="none" stroke="#fff" stroke-width="1"/></svg>
      info@verano.com
    </li>
    <li>
      <svg viewBox="0 0 11 11"><rect width="11" height="11" rx="2" fill="var(--brand-red)"/><circle cx="5.5" cy="5.5" r="3.2" fill="none" stroke="#fff" stroke-width="0.9"/><path d="M2.3 5.5 H8.7 M5.5 2.3 V8.7" stroke="#fff" stroke-width="0.8"/></svg>
      www.verano.com
    </li>
  </ul>

  <div class="address">Level 12, Harbour House<br>18 Quay Street, Sydney</div>
  <div class="services">Project Management - Acquisitions - Syndicates - Joint Venture</div>

  <div class="brand">VERANO PROPERTY</div>
</section>

<section class="card card-back" aria-label="Business card back">
  <svg class="card-graphics" viewBox="0 0 510 284" aria-hidden="true">
    <polygon points="0,132 0,148 136,284 152,284" fill="var(--white)"/>
    <polygon points="0,148 0,180 104,284 136,284" fill="var(--ink)"/>
    <polygon points="0,180 0,228 56,284 104,284" fill="var(--white)"/>
  </svg>

  <div class="brand">VERANO PROPERTY</div>
  <div class="back-web">www.verano.com</div>
</section>

</body>
</html>
```